Need Web Design for Business Process Outsourcing Company (Quorvane)

Quorvane is a business process outsourcing company. Need a simple site similar to http://www.tallowbrinkhire.com/ but with a more professional and credible look. New to the process; not sure where to start and comparing my options. Please let me know what my options are if I choose to go with you. Logo is attached for your reference. Please use same colorway

Reason: I want the final product to be coded. Please confirm you will be able to code final design.

Industry/Entity Type

Business

Coding

Coded - Design and coding required

```html
<!DOCTYPE html>
<html lang="en">
<head>
<meta charset="utf-8">
<title>Quorvane – Business Process Outsourcing</title>
<link rel="stylesheet" href="https://fonts.googleapis.com/css2?family=Lato:wght@300;400;700&display=swap">
<style>
:root{
  --brand:#1a8fc9;
  --brand-dark:#2c5f86;
  --footer:#2b6aa0;
  --ink:#222;
  --muted:#9a9a9a;
  --line:#dcdcdc;
  --soft:#f7f7f7;
  --white:#fff;
}
*{margin:0;padding:0;box-sizing:border-box}
html,body{width:1200px;height:2936px;overflow:hidden}
body{position:relative;font-family:"Lato",sans-serif;color:var(--ink);background:var(--white)}
.abs{position:absolute}

/* header */
.site-header{position:absolute;left:0;top:0;width:1200px;height:102px;background:var(--white)}
.brand{position:absolute;display:flex;align-items:center;gap:10px;font-weight:700;font-size:30px;color:var(--brand-dark)}
.brand-mark{width:34px;height:34px;background:var(--brand-dark)}
.site-header .brand{left:143px;top:34px}
.main-nav a{position:absolute;top:44px;font-size:13px;color:var(--ink);text-decoration:none}
.main-nav a.active{color:var(--brand)}

/* hero */
.hero{position:absolute;left:0;top:102px;width:1200px;height:534px;
  background:linear-gradient(100deg,#0e3552 0%,#1d5e84 40%,#154a6c 70%,#0b2a43 100%)}
.hero h1{position:absolute;left:200px;top:228px;font-weight:300;font-size:36px;color:var(--white)}
.hero p{position:absolute;left:200px;top:276px;font-weight:300;font-size:25px;color:var(--white)}
.hero .btn-ghost{left:204px;top:325px;width:127px;height:33px;border:1px solid var(--white);color:var(--white)}
.hero-dots{position:absolute;left:561px;top:398px;display:flex;gap:10px}
.hero-dots span{width:10px;height:10px;border-radius:50%;background:var(--white)}
.hero-dots span.on{background:var(--brand)}
.hero-tabs{position:absolute;left:8px;top:205px;display:flex;flex-direction:column;gap:6px}
.hero-tabs span{width:16px;height:17px;background:#2f7ab0;opacity:.7}

.btn-ghost{position:absolute;display:flex;align-items:center;justify-content:center;font-size:10px;letter-spacing:.5px;border:1px solid #b9b9b9;border-radius:2px;color:#777;text-transform:uppercase}

.section-title{position:absolute;left:0;width:1200px;text-align:center;font-weight:300;font-size:38px;color:var(--brand)}

/* services */
.service h3{position:absolute;font-weight:400;font-size:19px;color:var(--ink)}
.service p{position:absolute;width:370px;font-size:11.5px;line-height:25.5px;color:var(--muted)}
.service svg{position:absolute}
.service .btn-ghost{width:100px;height:33px}

.rule{position:absolute;left:145px;width:910px;height:1px;background:var(--line)}

.map{position:absolute;left:294px;top:1478px;width:610px;height:303px;
  background:radial-gradient(ellipse at 35% 40%,#e4e4e4 0%,#ececec 45%,rgba(255,255,255,0) 75%),
             radial-gradient(ellipse at 70% 45%,#e2e2e2 0%,#ededed 45%,rgba(255,255,255,0) 75%)}
.experience-copy{position:absolute;left:147px;top:1831px;width:906px;text-align:center;font-size:11px;line-height:25.5px;color:var(--muted)}

/* news */
.news{position:absolute;left:0;top:2078px;width:1200px;height:521px;background:var(--soft)}
.news-card .date{position:absolute;width:100px;height:113px}
.date .top{height:80px;background:var(--brand);color:var(--white);text-align:center;padding-top:4px}
.date .day{font-size:46px;font-weight:300;line-height:48px}
.date .mon{font-size:13px;text-transform:uppercase}
.date .year{height:33px;background:var(--brand-dark);color:var(--white);text-align:center;font-size:19px;line-height:33px}
.news-card h4{position:absolute;width:320px;font-weight:400;font-size:20px;line-height:25px;color:#8d8d8d}
.news-card p{position:absolute;width:320px;font-size:11.5px;line-height:26px;color:var(--muted)}
.pager{position:absolute;top:2548px;font-size:22px;color:var(--ink)}

/* footer */
.site-footer{position:absolute;left:0;top:2599px;width:1200px;height:337px;background:var(--footer);color:var(--white)}
.site-footer .brand{left:143px;top:56px;color:var(--white)}
.site-footer .brand-mark{background:var(--white)}
.foot-col{position:absolute;top:62px}
.foot-col h5{font-weight:400;font-size:14px;color:#cfe6f6;margin-bottom:22px}
.foot-col li{list-style:none;font-size:11px;line-height:24px}
.foot-col li.link::before{content:"›";margin-right:12px}
.social{display:flex;gap:10px}
.social span{width:12px;height:12px;border-radius:50%;background:var(--white)}
.copyright{position:absolute;left:0;top:2903px;width:1200px;text-align:center;font-size:11px;color:var(--white)}
</style>
</head>
<body>

<header class="site-header">
  <div class="brand"><span class="brand-mark"></span>Quorvane</div>
  <nav class="main-nav">
    <a class="active" style="left:650px">Home</a>
    <a style="left:712px">About Us</a>
    <a style="left:791px">Services</a>
    <a style="left:867px">News</a>
    <a style="left:926px">Projects</a>
    <a style="left:998px">Contact Us</a>
  </nav>
</header>

<section class="hero" role="img" aria-label="Business people walking through a bright glass office lobby, blue tinted">
  <div class="hero-tabs"><span></span><span></span><span></span><span></span></div>
  <h1>We are a BPO</h1>
  <p>Business Process Outsourcing</p>
  <div class="btn-ghost">Learn More</div>
  <div class="hero-dots"><span class="on"></span><span></span><span></span><span></span></div>
</section>

<h2 class="section-title" style="top:727px">What We Do?</h2>

<div class="service">
  <svg style="left:176px;top:858px" width="22" height="16" viewBox="0 0 22 16"><rect x="1" y="1" width="20" height="14" rx="2" fill="none" stroke="#1a8fc9" stroke-width="2"/><circle cx="11" cy="8" r="3.5" fill="#1a8fc9"/></svg>
  <h3 style="left:213px;top:855px">Finance &amp; Accounting</h3>
  <p style="left:217px;top:902px">Sed ut perspiciatis unde omnis iste natus error sit voluptatem accusan-tium doloremque laudantium, totam rem aperiam, eaque ipsa quae ab illo inventore veritatis et quasi architecto beatae</p>
  <div class="btn-ghost" style="left:217px;top:994px">Learn More</div>
</div>
<div class="service">
  <svg style="left:630px;top:856px" width="22" height="18" viewBox="0 0 22 18"><path d="M1 1v16h20" fill="none" stroke="#1a8fc9" stroke-width="2"/><rect x="5" y="8" width="3" height="7" fill="#1a8fc9"/><rect x="10" y="4" width="3" height="11" fill="#1a8fc9"/><rect x="15" y="7" width="3" height="8" fill="#1a8fc9"/></svg>
  <h3 style="left:681px;top:855px">Marketing</h3>
  <p style="left:681px;top:902px">Sed ut perspiciatis unde omnis iste natus error sit voluptatem accusan-tium doloremque laudantium, totam rem aperiam, eaque ipsa quae ab illo inventore veritatis et quasi architecto beatae</p>
  <div class="btn-ghost" style="left:681px;top:994px">Learn More</div>
</div>
<div class="service">
  <svg style="left:176px;top:1085px" width="22" height="20" viewBox="0 0 22 20"><path d="M11 19 2 10C-1 6 2 1 6 1c2 0 4 1 5 3 1-2 3-3 5-3 4 0 7 5 4 9z" fill="#1a8fc9"/></svg>
  <h3 style="left:213px;top:1082px">Health</h3>
  <p style="left:217px;top:1133px">Sed ut perspiciatis unde omnis iste natus error sit voluptatem accusan-tium doloremque laudantium, totam rem aperiam, eaque ipsa quae ab illo inventore veritatis et quasi architecto beatae</p>
  <div class="btn-ghost" style="left:217px;top:1229px">Learn More</div>
</div>
<div class="service">
  <svg style="left:632px;top:1083px" width="18" height="22" viewBox="0 0 18 22"><path d="M1 1h11l5 5v15H1z" fill="none" stroke="#1a8fc9" stroke-width="2"/><path d="M5 10h8M5 14h8M5 18h6" stroke="#1a8fc9" stroke-width="1.6"/></svg>
  <h3 style="left:681px;top:1082px">Insurance</h3>
  <p style="left:681px;top:1133px">Sed ut perspiciatis unde omnis iste natus error sit voluptatem accusan-tium doloremque laudantium, totam rem aperiam, eaque ipsa quae ab illo inventore veritatis et quasi architecto beatae</p>
  <div class="btn-ghost" style="left:681px;top:1229px">Learn More</div>
</div>

<div class="rule" style="top:1323px"></div>

<h2 class="section-title" style="top:1378px">Our Global Experience</h2>
<div class="map" role="img" aria-label="Dotted grey world map"></div>
<p class="experience-copy">Sed ut perspiciatis unde omnis iste natus error sit voluptatem accusantium doloremque laudantium, totam rem aperiam, eaque ipsa quae ab illo inventore veritatis et quasi archi-tecto beatae vitae dicta sunt explicabo. Nemo enim ipsam voluptatem quia voluptas sit aspernatur aut odit aut fugit, sed quia consequuntur magni dolores eos qui ratione volup-tatem Sed ut perspiciatis unde omnis iste natus error sit voluptatem accusantium doloremque laudantium</p>
<div class="btn-ghost" style="left:524px;top:1951px;width:151px;height:34px">Contact Us</div>

<section class="news">
  <h2 class="section-title" style="top:45px">Latest News</h2>
  <div class="rule" style="top:116px"></div>

  <article class="news-card">
    <div class="date" style="left:145px;top:175px">
      <div class="top"><div class="day">5</div><div class="mon">Nov</div></div>
      <div class="year">2016</div>
    </div>
    <h4 style="left:260px;top:172px">Sed ut perspiciatis unde omnis iste natus error sit voluptatem accusantium doloremque laudantium</h4>
    <p style="left:260px;top:303px">Aque ipsa quae ab illo inventore veritatis et quasi architecto beatae vitae dicta sunt explicabo. Nemo enim ipsam voluptatem quia voluptas sit aspernatur aut odit aut fugit, sed quia consequuntur magni dolores</p>
  </article>
  <article class="news-card">
    <div class="date" style="left:611px;top:175px">
      <div class="top"><div class="day">5</div><div class="mon">Nov</div></div>
      <div class="year">2016</div>
    </div>
    <h4 style="left:726px;top:172px">Sed ut perspiciatis unde omnis iste natus error sit voluptatem accusantium doloremque laudantium</h4>
    <p style="left:726px;top:303px">Aque ipsa quae ab illo inventore veritatis et quasi architecto beatae vitae dicta sunt explicabo. Nemo enim ipsam voluptatem quia voluptas sit aspernatur aut odit aut fugit, sed quia consequuntur magni dolores</p>
  </article>
</section>
<svg class="pager" style="left:578px" width="14" height="20" viewBox="0 0 14 20"><path d="M10 3 4 10l6 7" fill="none" stroke="#222" stroke-width="2.4"/></svg>
<svg class="pager" style="left:608px" width="14" height="20" viewBox="0 0 14 20"><path d="M4 3l6 7-6 7" fill="none" stroke="#222" stroke-width="2.4"/></svg>

<footer class="site-footer">
  <div class="brand"><span class="brand-mark"></span>Quorvane</div>
  <div class="foot-col" style="left:391px">
    <h5>Quick Links</h5>
    <ul><li class="link">Home</li><li class="link">About Us</li><li class="link">Services</li><li class="link">News</li><li class="link">Projects</li><li class="link">Contact Us</li></ul>
  </div>
  <div class="foot-col" style="left:552px">
    <h5>Other Links</h5>
    <ul><li class="link">Terms Of Use</li><li class="link">Privacy Policy</li><li class="link">Help</li><li class="link">Disclaimer</li></ul>
  </div>
  <div class="foot-col" style="left:716px">
    <h5>Contact Us</h5>
    <ul><li>Hallmark Bureau</li><li>Lindenweg 12</li><li>10115 Berlin</li><li>E-Mail: info@quorvane.com</li></ul>
  </div>
  <div class="foot-col" style="left:867px">
    <h5>Connect With Us</h5>
    <div class="social"><span></span><span></span><span></span><span></span><span></span></div>
  </div>
</footer>
<p class="copyright">© 2016 Company Name | &nbsp;All Rights Reserved</p>

</body>
</html>
```